Start my own business with coaching / consulting / hypnosis website (www.marcoveltrup.de) and need

These graphics should represent the process of a coaching / floatpulse / high-performance coaching / hypnosis session, which I conduct with the client. The client should get easier and simpler idea of ​​WHAT exactly happens in such a session and HOW it happens. The customer should always have a positive added value and benefit for him. So the customer leaves the session satisfied and happy and can easily master his initial challenge. The categories I need are: -Coaching -solution finding-entanglements / dependencies -Floatpulse Coaching -high-performance coaching -Hypnosis Session -counselling / couple counseling -Systemic installation Please, 3 to 4 pictures each characterizing the process of the individual categories from beginning to end. Since the beginning and the end of the process, I only need the changing middle part. As a male coach, so please include me in the pictures. --Coaching ----- 3-4 pictures -Clarify the issue -Expand perspectives and options / find the way to a solution for the solution -Finally finding and integrating the right solution -customer is happy and goodbye - -solution-finding --------- 1 picture The only thing that becomes clear is that the solution is read with the client, who usually does not see this solution, or it is not visible to him or the client discovers it means the help of the coach, he can also use it. -Enmeschments / Dependencies ----- 1 Picture picture where clearly people often have entanglements / dependencies on other people / things and thus often in a child of entanglements, which in turn to influence this person. --Floatpulse ----- Middle part: 1 picture -Clarify the issue -Expand perspectives and options / find the way to a solution / set to impulse for the solution -Seat in front of each other and initiate the manual REM phase with the hand of the coach. -customer is Happy and goodbye High Performance Coaching -------- middle section 1-2 pictures -Clarify the issue -Expand perspectives and options / find the way to a solution / set to impulse for the solution -Recognize and awaken potentials in the client ---> superwoman / ironhawk (the gesture where ironhawk tears his shirt is open and underneath his ironhawk sign gets visible on his chest) -customer is happy and goodbye-hypnosis session ----- middle section 1 -2 pictures -Clarify the issue -Expand perspectives and options / find the way to a solution for the solution -both sit relaxed in the armchair -Hypnosis is carried out: Coach speaks to the client, who closes his eyes and imagines the situation in the unconscious. -customer is happy and goodbye --Consulting / Couples consulting / Relationship consulting ----- 3-4 pictures -person / couple comes with concerns, clarifies -expand perspectives and options / find the way to a solution / set impulse for the solution -imparting new knowledge, lovingly talking about it, interaction of the couple, it may also be fun and easy-perspectives -customer / couple is happy and says goodbye - Systemic Constellation- 1-2 Pictures -person / couple comes with concerns, these concerns clarify -other persons are placed in a room and represent persons / family members / personal shares -the solution to the problem itself-to-be-happy

```html
<!DOCTYPE html>
<html lang="en">
<head>
<meta charset="utf-8">
<title>Marco Veltrup – Coaching, Consulting, Hypnosis</title>
<link rel="stylesheet" href="https://fonts.googleapis.com/css2?family=Cinzel:wght@400;700&family=Lato:wght@400;700&display=swap">
<style>
:root{
  --orange:#e8611f;
  --orange-dark:#d4551a;
  --ink:#2b2b2b;
  --muted:#777;
  --white:#fff;
  --black:#111;
  --serif:'Cinzel', Georgia, serif;
  --sans:'Lato', Arial, sans-serif;
}
*{box-sizing:border-box;margin:0;padding:0}
html,body{width:1200px;height:3203px;overflow:hidden}
body{position:relative;font-family:var(--sans);color:var(--ink);background:var(--white)}
.abs{position:absolute}

/* header */
.site-header{position:absolute;left:0;top:0;width:1200px;height:100px;background:var(--white);border-top:4px solid var(--orange)}
.brand{position:absolute;left:110px;top:28px;font-family:var(--serif);font-size:34px;color:var(--ink);letter-spacing:1px}
.main-nav{position:absolute;top:44px;left:0;width:1200px}
.main-nav span{position:absolute;transform:translateX(-50%);font-family:var(--serif);font-size:16px;color:var(--ink);white-space:nowrap}
.main-nav .active{color:var(--orange)}

/* hero */
.hero{position:absolute;left:0;top:100px;width:1200px;height:550px}
.hero-photo{position:absolute;inset:0;background:linear-gradient(120deg,#cfc9c2 0%,#8a6d58 30%,#4b4a4c 60%,#2f3238 100%)}
.hero-shade{position:absolute;inset:0;background:rgba(20,20,20,.35)}
.hero-title{position:absolute;top:206px;width:100%;text-align:center;font-family:var(--serif);font-weight:700;font-size:60px;color:var(--white);letter-spacing:1px}
.hero-tagline{position:absolute;top:304px;width:100%;text-align:center;font-family:var(--serif);font-size:26px;color:var(--white);letter-spacing:4px}
.hero-tagline .dot{display:inline-block;width:10px;height:10px;border-radius:50%;background:var(--orange);margin:0 10px;vertical-align:middle}
.scroll-cue{position:absolute;left:586px;top:460px}

/* about */
.about{position:absolute;left:0;top:650px;width:1200px;height:568px;background:radial-gradient(circle at 875px 280px,#ffffff 0%,#f6f6f6 60%,#f1f1f1 100%)}
.section-title{font-family:var(--serif);font-weight:400;color:var(--ink)}
.about .section-title{position:absolute;left:122px;top:112px;font-size:44px}
.about-text{position:absolute;left:122px;top:188px;width:490px;font-size:13px;line-height:32px;color:var(--muted)}
.btn-read{position:absolute;left:122px;top:388px;width:152px;height:44px;border-radius:22px;background:var(--orange);color:var(--white);font-weight:700;font-size:14px;text-align:center;line-height:44px}
.portrait-ring{position:absolute;left:665px;top:72px;width:414px;height:414px;border-radius:50%;border:8px solid var(--orange);border-left-color:transparent;transform:rotate(20deg)}
.portrait{position:absolute;left:675px;top:86px;width:384px;height:384px;border-radius:50%;background:linear-gradient(160deg,#d9dde2 0%,#8a8f98 45%,#2e3440 100%)}

/* categories */
.categories{position:absolute;left:0;top:1218px;width:1200px;height:1169px;background:linear-gradient(135deg,#f2f2f2 0%,#e9e9e9 50%,#f2f2f2 100%)}
.categories .section-title{position:absolute;top:112px;width:100%;text-align:center;font-size:40px}
.tile{position:absolute;width:222px;height:194px;background:var(--white);box-shadow:0 2px 6px rgba(0,0,0,.08);text-align:center}
.tile svg{position:absolute;left:76px;top:26px}
.tile-label{position:absolute;left:0;width:100%;top:122px;font-family:var(--serif);font-size:15px;line-height:26px;color:var(--ink)}
.tile.is-active{background:var(--orange)}
.tile.is-active .tile-label{color:var(--white)}
.step-label{position:absolute;transform:translateX(-50%);text-align:center;font-size:14px;line-height:26px;color:var(--ink);white-space:nowrap}

/* contact */
.contact{position:absolute;left:0;top:2387px;width:1200px;height:566px;background:radial-gradient(circle at 600px 300px,#ee6b28 0%,var(--orange) 60%,var(--orange-dark) 100%)}
.contact .section-title{position:absolute;top:72px;width:100%;text-align:center;font-size:44px;color:var(--white)}
.field{position:absolute;background:var(--white);font-size:12px;color:#555;padding:16px 24px;letter-spacing:.5px}
.btn-submit{position:absolute;left:520px;top:440px;width:160px;height:46px;border-radius:23px;background:var(--black);color:var(--white);font-weight:700;font-size:17px;text-align:center;line-height:46px}

/* footer */
.site-footer{position:absolute;left:0;top:2953px;width:1200px;height:250px;background:var(--black)}
.social{position:absolute;top:35px;width:56px;height:56px;border:3px solid var(--white);border-radius:50%;color:var(--white);font-family:var(--sans);font-weight:700;font-size:13px;text-align:center;line-height:50px}
.footer-rule{position:absolute;left:490px;top:121px;width:220px;height:1px;background:#444}
.footer-nav{position:absolute;top:152px;width:100%;text-align:center;font-family:var(--serif);font-size:16px;color:var(--white)}
.footer-nav i{display:inline-block;width:4px;height:4px;border-radius:50%;background:#888;margin:0 16px;vertical-align:middle}
.copyright{position:absolute;top:202px;width:100%;text-align:center;font-size:11px;color:#aaa}
</style>
</head>
<body>

<header class="site-header">
  <div class="brand">Marco Veltrup</div>
  <nav class="main-nav">
    <span class="active" style="left:542px">Home</span>
    <span style="left:656px">About Me</span>
    <span style="left:793px">Categories</span>
    <span style="left:912px">Blog</span>
    <span style="left:1035px">Contact Me</span>
  </nav>
</header>

<section class="hero">
  <div class="hero-photo" role="img" aria-label="Photo of a coach and a client talking, hands and clipboard in close view"></div>
  <div class="hero-shade"></div>
  <h1 class="hero-title">Marco Veltrup</h1>
  <p class="hero-tagline">COACHING<span class="dot"></span>CONSULTING<span class="dot"></span>HYPNOSIS</p>
  <svg class="scroll-cue" width="28" height="52" viewBox="0 0 28 52" fill="none" stroke="#fff" stroke-width="2">
    <rect x="4" y="1" width="20" height="32" rx="10"/>
    <line x1="14" y1="8" x2="14" y2="14"/>
    <polyline points="8,38 14,44 20,38"/>
    <polyline points="8,44 14,50 20,44"/>
  </svg>
</section>

<section class="about">
  <h2 class="section-title">About Me</h2>
  <p class="about-text">At vero eos et accusamus et iusto odio dignissimos ducimus qui blanditiis praesentium voluptatum deleniti atque corrupti quos dolores et quas molestias excepturi sint occaecati cupiditate non provident, similique sunt in culpa qui officia deserunt mollitia animi, id est laborum et dolorum fuga. Et harum quidem rerum facilis est et expedita distinctio. Nam libero tempore, cum soluta nobis est eligendi optio cumqu..</p>
  <div class="btn-read">READ MORE</div>
  <div class="portrait-ring"></div>
  <div class="portrait" role="img" aria-label="Portrait photo of the coach in a suit at a desk with a laptop"></div>
</section>

<section class="categories">
  <h2 class="section-title">CATEGORIES</h2>

  <div class="tile is-active" style="left:113px;top:219px">
    <svg width="70" height="70" viewBox="0 0 70 70" fill="none" stroke="#fff" stroke-width="2"><circle cx="35" cy="14" r="6"/><path d="M22 8l13 20 13-20M35 28v14"/><circle cx="16" cy="42" r="5"/><circle cx="54" cy="42" r="5"/><path d="M6 62c0-8 5-12 10-12s10 4 10 12M44 62c0-8 5-12 10-12s10 4 10 12M26 62c0-10 4-18 9-18s9 8 9 18"/></svg>
    <div class="tile-label">Coaching</div>
  </div>
  <div class="tile" style="left:363px;top:219px">
    <svg width="70" height="70" viewBox="0 0 70 70" fill="none" stroke="#222" stroke-width="2"><circle cx="35" cy="32" r="13"/><path d="M29 45h12v8H29zM35 6v8M12 32H4M66 32h-8M18 15l-5-5M52 15l5-5"/><circle cx="35" cy="32" r="4" fill="#e8611f" stroke="none"/></svg>
    <div class="tile-label">Solution Finding</div>
  </div>
  <div class="tile" style="left:613px;top:219px">
    <svg width="70" height="70" viewBox="0 0 70 70" fill="none" stroke="#222" stroke-width="2"><rect x="6" y="6" width="58" height="58"/><path d="M35 6v20a5 5 0 010 10v28M6 35h20a5 5 0 0110 0h28"/><rect x="14" y="14" width="12" height="12" fill="#e8611f" stroke="none"/></svg>
    <div class="tile-label">Entanglements<br>Dependencies</div>
  </div>
  <div class="tile" style="left:863px;top:219px">
    <svg width="70" height="70" viewBox="0 0 70 70" fill="none" stroke="#222" stroke-width="2"><circle cx="35" cy="16" r="7"/><path d="M35 4v-2M22 16h-8M56 16h-8M35 30v-6"/><polyline points="18,12 14,16 18,20"/><polyline points="52,12 56,16 52,20"/><path d="M27 66V42c0-6 4-10 8-10s8 4 8 10v24"/><circle cx="35" cy="16" r="2" fill="#e8611f" stroke="none"/></svg>
    <div class="tile-label">Floatpulse<br>Coaching</div>
  </div>

  <div class="tile" style="left:113px;top:449px">
    <svg width="70" height="70" viewBox="0 0 70 70" fill="none" stroke="#222" stroke-width="2"><rect x="8" y="6" width="54" height="30"/><path d="M14 28l10-8 8 6 12-12" stroke="#e8611f"/><circle cx="35" cy="46" r="6"/><path d="M24 66c0-8 5-13 11-13s11 5 11 13M20 36v8M50 36v8"/></svg>
    <div class="tile-label">high-performance<br>coaching</div>
  </div>
  <div class="tile" style="left:363px;top:449px">
    <svg width="70" height="70" viewBox="0 0 70 70" fill="none" stroke="#222" stroke-width="2"><circle cx="35" cy="37" r="27"/><path d="M35 10v6M35 37l-10-12" stroke-width="3"/><circle cx="35" cy="37" r="3" fill="#e8611f" stroke="none"/></svg>
    <div class="tile-label">Hypnosis Session</div>
  </div>
  <div class="tile" style="left:613px;top:449px">
    <svg width="70" height="70" viewBox="0 0 70 70" fill="none" stroke="#222" stroke-width="2"><circle cx="26" cy="34" r="8"/><path d="M10 64c0-10 7-16 16-16s16 6 16 16"/><path d="M40 6h24v16H52l-6 6v-6h-6z"/><circle cx="46" cy="14" r="1.5" fill="#e8611f"/><circle cx="52" cy="14" r="1.5" fill="#e8611f"/><circle cx="58" cy="14" r="1.5" fill="#e8611f"/></svg>
    <div class="tile-label">Counselling /<br>couple counselling</div>
  </div>
  <div class="tile" style="left:863px;top:449px">
    <svg width="70" height="70" viewBox="0 0 70 70" fill="none" stroke="#222" stroke-width="2"><circle cx="35" cy="35" r="26"/><circle cx="35" cy="35" r="18"/><circle cx="35" cy="35" r="8" fill="#e8611f" stroke="none"/><path d="M35 2v12M35 56v12M2 35h12M56 35h12"/></svg>
    <div class="tile-label">Systemic<br>installation</div>
  </div>

  <svg class="abs" style="left:0;top:0" width="1200" height="1169" viewBox="0 0 1200 1169" fill="none">
    <path d="M113 414 C60 560 10 720 78 830" stroke="#e8611f" stroke-width="1.5" stroke-dasharray="6 5"/>
    <polygon points="80,838 72,826 84,826" fill="#e8611f"/>
    <path d="M298 858c14-6 30-4 42 8" stroke="#222" stroke-width="1.6"/><polyline points="334,862 341,868 333,870" stroke="#222" stroke-width="1.6"/>
    <path d="M554 906c16 6 30 2 42-8" stroke="#222" stroke-width="1.6"/><polyline points="588,896 597,897 594,905" stroke="#222" stroke-width="1.6"/>
    <path d="M890 852c14-6 28-4 40 6" stroke="#222" stroke-width="1.6"/><polyline points="924,852 931,859 923,861" stroke="#222" stroke-width="1.6"/>

    <!-- step 1: board -->
    <g stroke-width="2.5">
      <rect x="142" y="784" width="64" height="44" stroke="#222"/>
      <rect x="152" y="792" width="14" height="10" fill="#e8611f" stroke="#222" stroke-width="1.5"/>
      <rect x="152" y="810" width="14" height="10" fill="#e8611f" stroke="#222" stroke-width="1.5"/>
      <path d="M172 798h22M172 814h22M160 828l-8 20M190 828l8 20" stroke="#222"/>
      <circle cx="214" cy="798" r="7" fill="#e8611f" stroke="#222" stroke-width="1.5"/>
      <path d="M204 848v-28c0-6 20-6 20 0v28" fill="#e8611f" stroke="#222" stroke-width="1.5"/>
    </g>
    <!-- step 2: chain link -->
    <g transform="rotate(45 448 921)" stroke="#222" stroke-width="7" fill="none">
      <rect x="414" y="910" width="40" height="22" rx="11"/>
      <rect x="442" y="910" width="40" height="22" rx="11"/>
    </g>
    <!-- step 3: magnifier -->
    <g>
      <circle cx="742" cy="812" r="22" stroke="#222" stroke-width="4"/>
      <path d="M758 828l18 18" stroke="#222" stroke-width="6" stroke-linecap="round"/>
      <circle cx="742" cy="808" r="8" fill="#e8611f"/>
      <path d="M736 812l6 14 6-14z" fill="#e8611f"/>
    </g>
    <!-- step 4: smile -->
    <g>
      <circle cx="1005" cy="919" r="34" stroke="#222" stroke-width="3"/>
      <path d="M986 904c0-6 9-6 9 0 0-6 9-6 9 0 0 6-9 12-9 12s-9-6-9-12zM1006 904c0-6 9-6 9 0 0-6 9-6 9 0 0 6-9 12-9 12s-9-6-9-12z" fill="#e8611f" transform="translate(-3 0)"/>
      <path d="M988 930c8 12 26 12 34 0" stroke="#222" stroke-width="3" stroke-linecap="round"/>
    </g>
  </svg>

  <div class="step-label" style="left:184px;top:878px">Clarify the issue</div>
  <div class="step-label" style="left:448px;top:982px">Expand perspectives and options<br>/ find the way to a solution /<br>set an impulse for the solution</div>
  <div class="step-label" style="left:747px;top:878px">Finally finding and integrating<br>the right solution</div>
  <div class="step-label" style="left:1005px;top:986px">customer is Happy<br>and goodbye</div>
</section>

<section class="contact">
  <h2 class="section-title">Contact Me</h2>
  <div class="field" style="left:203px;top:166px;width:384px;height:52px">ENTER NAME</div>
  <div class="field" style="left:613px;top:166px;width:384px;height:52px">ENTER EMAIL</div>
  <div class="field" style="left:203px;top:235px;width:384px;height:52px">PHONE</div>
  <div class="field" style="left:613px;top:235px;width:384px;height:52px">ADDRESS</div>
  <div class="field" style="left:203px;top:303px;width:794px;height:98px">MESSAGE</div>
  <div class="btn-submit">SUBMIT
    <svg width="18" height="18" viewBox="0 0 18 18" style="vertical-align:-3px;margin-left:6px"><circle cx="9" cy="9" r="8" fill="#fff"/><path d="M7 5l4 4-4 4" stroke="#111" stroke-width="2" fill="none"/></svg>
  </div>
</section>

<footer class="site-footer">
  <div class="social" style="left:461px">Page</div>
  <div class="social" style="left:540px">Post</div>
  <div class="social" style="left:620px">Feed</div>
  <div class="social" style="left:699px">Net</div>
  <div class="footer-rule"></div>
  <div class="footer-nav">Home<i></i>About Me<i></i>Categories<i></i>Blog<i></i>Contact Me</div>
  <div class="copyright">All Rights Reserved .Copyrights2018 @companyname.com</div>
</footer>

</body>
</html>
```